business card for horse saddlery

after a new business card for our saddlery, i will add 2 logos we have previously used and they can be used (or not) . Any images can be used from our website also at www.harrowfields.net.au, I have also added our brand logo, which may be good to incorporate on back ? we have over 15, 000 items online, ship Australia Wide.

Target Market(s)

horse owners

Industry/Entity Type

Retail - Equestrian

Contact Information for Business Card

Harrowfield Horse Supplies, 1300 48 62 90, www.harrowfields.net.au, 27 Lindqvist Rd Marrowbank Q 4587

Requirements
Must have
• trailgem is our brand so trailgem logo on back as 'distributers of', easy to read
Nice to have
• professional but fun
Should not have
• double sided (description wont save double sided)

```html
<!DOCTYPE html>
<html lang="en">
<head>
<meta charset="utf-8">
<title>Harrowfield Horse Supplies – Business Card</title>
<link href="https://fonts.googleapis.com/css2?family=Open+Sans:wght@400;600;700;800&display=swap" rel="stylesheet">
<style>
  :root {
    --stage: #232323;
    --navy: #283e7a;
    --gold: #fdb31c;
    --white: #ffffff;
    --card-dark: #1d1d21;
    --layer-mid: #24242a;
    --layer-low: #2b2b31;
    --icon-blue: #4d8fd6;
    --muted-blue: #3f6fb8;
    --muted-grey: #8d96a3;
  }
  * { box-sizing: border-box; margin: 0; padding: 0; }
  html, body { width: 1200px; height: 780px; overflow: hidden; }
  body {
    background: var(--stage);
    font-family: "Open Sans", Arial, sans-serif;
    position: relative;
  }
  .card {
    position: absolute;
    top: 80px;
    width: 360px;
    height: 620px;
    border-radius: 26px;
    overflow: hidden;
    box-shadow: 0 18px 40px rgba(0,0,0,.55);
  }
  /* Back of card */
  .card-back { left: 190px; background: var(--navy); }
  .back-brand {
    position: absolute;
    left: 0; right: 0; top: 230px;
    display: flex; flex-direction: column; align-items: center;
  }
  .brand-disc {
    width: 120px; height: 120px; border-radius: 50%;
    background: var(--gold);
    margin-bottom: 22px;
  }
  .back-brand-name {
    color: var(--white);
    font-weight: 600;
    font-size: 30px;
    line-height: 1.15;
    text-align: center;
  }
  /* Front of card */
  .card-front { left: 650px; background: var(--card-dark); }
  .front-layers { position: absolute; inset: 0; }
  .front-brand {
    position: absolute; top: 48px; left: 0; right: 0;
    display: flex; align-items: center; justify-content: center; gap: 10px;
  }
  .front-brand-dot { width: 22px; height: 22px; border-radius: 50%; background: var(--gold); }
  .front-brand-name { color: var(--muted-blue); font-weight: 600; font-size: 19px; }
  .portrait {
    position: absolute; top: 112px; left: 50%;
    width: 130px; height: 130px; margin-left: -65px;
    border-radius: 50%;
    border: 3px solid var(--gold);
    background: radial-gradient(circle at 45% 45%, #d9dbdf 0%, #a7aab0 38%, #2b2b2e 72%, #0c0c0d 100%);
  }
  .contact {
    position: absolute; top: 262px; left: 0; right: 0;
    text-align: center; color: var(--white);
  }
  .person-name { color: var(--gold); font-weight: 800; font-size: 28px; letter-spacing: .3px; }
  .person-role { font-weight: 600; font-size: 15px; margin-top: 2px; }
  .icon-row { display: flex; justify-content: center; gap: 14px; margin: 10px 0 6px; }
  .icon { width: 20px; height: 20px; }
  .phone { font-weight: 700; font-size: 24px; letter-spacing: .5px; }
  .web { font-weight: 600; font-size: 15px; margin-top: 2px; }
  .pin-row { margin: 14px 0 4px; display: flex; justify-content: center; }
  .address { font-weight: 600; font-size: 15px; line-height: 1.35; }
  .partners {
    position: absolute; bottom: 52px; left: 0; right: 0;
    display: flex; justify-content: center; align-items: center; gap: 34px;
  }
  .partner-harrowfield { color: var(--icon-blue); font-weight: 600; font-size: 15px; }
  .partner-trailgem { color: var(--muted-grey); font-weight: 600; font-size: 17px; text-transform: uppercase; letter-spacing: 1px; }
</style>
</head>
<body>

<section class="card card-back" aria-label="Card back">
  <div class="back-brand">
    <div class="brand-disc"></div>
    <p class="back-brand-name">Harrowfield<br>Horse Supplies</p>
  </div>
</section>

<section class="card card-front" aria-label="Card front">
  <svg class="front-layers" width="360" height="620" viewBox="0 0 360 620" aria-hidden="true">
    <defs>
      <filter id="layer-shadow" x="-20%" y="-20%" width="140%" height="140%">
        <feDropShadow dx="0" dy="6" stdDeviation="8" flood-color="#000" flood-opacity=".55"/>
      </filter>
    </defs>
    <rect width="360" height="620" fill="var(--layer-low)"/>
    <path d="M0 0 H360 V470 C300 560 160 560 0 520 Z" fill="var(--layer-mid)" filter="url(#layer-shadow)"/>
    <path d="M0 0 H360 V420 C320 500 180 520 0 490 Z" fill="var(--card-dark)" filter="url(#layer-shadow)"/>
  </svg>

  <div class="front-brand">
    <span class="front-brand-dot"></span>
    <span class="front-brand-name">Harrowfield Horse Supplies</span>
  </div>

  <div class="portrait" role="img" aria-label="Photo of a white horse wearing a bridle on a black background"></div>

  <div class="contact">
    <p class="person-name">Marta Lindholm</p>
    <p class="person-role">Horse owners</p>
    <div class="icon-row">
      <svg class="icon" viewBox="0 0 20 20" aria-label="Phone">
        <circle cx="10" cy="10" r="9" fill="var(--icon-blue)" stroke="#fff" stroke-width="1.5"/>
        <path d="M7 5.5l1.6 2.4-1 1c.6 1.3 1.6 2.3 2.9 2.9l1-1 2.4 1.6-.8 1.6c-3.6-.3-6.5-3.2-6.8-6.8z" fill="#fff"/>
      </svg>
      <svg class="icon" viewBox="0 0 20 20" aria-label="Website">
        <circle cx="10" cy="10" r="9" fill="var(--icon-blue)" stroke="#fff" stroke-width="1.5"/>
        <circle cx="10" cy="10" r="5" fill="none" stroke="#fff" stroke-width="1.2"/>
        <path d="M5 10h10M10 5c-2 2.8-2 7.2 0 10M10 5c2 2.8 2 7.2 0 10" fill="none" stroke="#fff" stroke-width="1"/>
      </svg>
    </div>
    <p class="phone">1300 48 62 90</p>
    <p class="web">www.harrowfields.net.au</p>
    <div class="pin-row">
      <svg class="icon" viewBox="0 0 20 20" aria-label="Address">
        <circle cx="10" cy="10" r="9" fill="var(--icon-blue)" stroke="#fff" stroke-width="1.5"/>
        <path d="M10 4.5a3.5 3.5 0 0 0-3.5 3.5c0 2.6 3.5 7 3.5 7s3.5-4.4 3.5-7A3.5 3.5 0 0 0 10 4.5z" fill="#fff"/>
        <circle cx="10" cy="8" r="1.3" fill="var(--icon-blue)"/>
      </svg>
    </div>
    <p class="address">27 Lindqvist Rd<br>Marrowbank Q 4587</p>
  </div>

  <div class="partners">
    <span class="partner-harrowfield">Harrowfield</span>
    <span class="partner-trailgem">trailgem</span>
  </div>
</section>

</body>
</html>
```